Modern Label for cleaning products for the brand Vorlix

We need a label design for our line of cleaning products. The label should feature our logo and an image to identify the product's intended use. I've added our logo and an image for use. This only concerns the design of the label on the front of the bottle.

Label dimensions:
Label 1 (500ml bottle with spray): width 58mm x height 115mm
Label 2: (1L bottle): width 73mm x height 140mm
The design must be consistent for both bottles which you find in the pictures.

The bottles to be labeled are white. See the attachment for a photo of the bottles.

The photo must also appear on the label to identify the product's intended use.

Product information:
Brand: Vorlix
Product: Sanitary Cleaner

This text must be placed on the label:
"Cleans, descales & freshens. followed with this text: "Ideal for quick and powerful cleaning. A ready-to-use product for everyday use."

- Mention the seperate USP's: Sanitary, Bathroom, Toilet, Wet areas

Appearance: This is a consumer product, but it must have a professional appearance. We would like to see a design that use the color blue from our logo.

Target Market(s)

Consumers who take care of their homes and want to maintain it the correct (professional) way

Font styles to use
Sans Serif

Colors
0054AA
0677BA
7BADD7
CADEEF
E8F1F8

Requirements
Must have
• USP's + use of image and logo + blend in 1 design
Nice to have
• Keep the color of the logo in the design
Should not have
• Comic sans

```html
<!DOCTYPE html>
<html lang="en">
<head>
<meta charset="utf-8">
<title>Vorlix Sanitary Cleaner – Front Labels</title>
<link rel="stylesheet" href="https://fonts.googleapis.com/css2?family=Montserrat:ital,wght@0,800;1,800;1,900&family=Oswald:wght@500;600&display=swap">
<style>
  :root {
    --brand-blue: #0054AA;
    --mid-blue: #0677BA;
    --soft-blue: #7BADD7;
    --pale-blue: #CADEEF;
    --mist-blue: #E8F1F8;
    --navy: #1B2A5C;
    --ink: #1A1D2E;
    --gold: #F5AE1B;
    --white: #FFFFFF;
    --page: #FFFFFF;
  }
  * { box-sizing: border-box; margin: 0; padding: 0; }
  h1, p { font-size: inherit; font-weight: inherit; }
  html, body { width: 767px; height: 1200px; overflow: hidden; background: var(--page); }

  .sheet {
    position: relative;
    width: 767px;
    height: 1200px;
    display: flex;
    align-items: flex-start;
    justify-content: center;
    gap: 70px;
    padding-top: 265px;
  }

  .label {
    position: relative;
    width: 100em;
    overflow: hidden;
    font-family: "Montserrat", sans-serif;
    color: var(--white);
    box-shadow: 0 1px 3px rgba(0,0,0,.18);
  }
  .label--500 { font-size: 2.77px; height: 197.8em; }
  .label--1l  { font-size: 3.49px; height: 191.7em; }

  .label-photo {
    position: absolute;
    inset: 0 0 36% 0;
    background:
      radial-gradient(ellipse 46% 30% at 52% 56%, #f4f6f8 0%, #dfe3e7 55%, rgba(200,215,230,0) 100%),
      radial-gradient(ellipse 60% 40% at 50% 22%, var(--white) 0%, rgba(255,255,255,0) 100%),
      linear-gradient(90deg, var(--soft-blue) 0%, var(--mist-blue) 22%, var(--white) 50%, var(--mist-blue) 78%, var(--soft-blue) 100%);
  }

  .label-band {
    position: absolute;
    left: 0; right: 0; top: 58%; bottom: 0;
    background: linear-gradient(180deg, rgba(6,119,186,.55) 0%, var(--mid-blue) 14%, var(--brand-blue) 45%, #0A3F8F 100%);
    clip-path: polygon(0 10%, 30% 4%, 65% 8%, 100% 0, 100% 100%, 0 100%);
  }

  .brand {
    position: absolute;
    left: 0; right: 0; top: 12%;
    display: flex;
    align-items: center;
    justify-content: center;
    gap: 4em;
  }
  .brand-dot {
    width: 13em; height: 13em;
    border-radius: 50%;
    background: var(--mid-blue);
  }
  .brand-name {
    font-weight: 800;
    font-size: 17em;
    letter-spacing: -0.02em;
    color: var(--ink);
    line-height: 1;
  }

  .germ-badge {
    position: absolute;
    right: 6%; top: 28%;
    width: 28%; height: 10%;
    border-radius: 50%;
    background: var(--navy);
    border: 0.6em solid var(--white);
    display: flex; flex-direction: column; align-items: center; justify-content: center;
    line-height: 0.95;
  }
  .germ-badge__kills { font-weight: 800; font-size: 5.6em; }
  .germ-badge__rate { font-family: "Oswald", sans-serif; font-weight: 600; font-size: 7.4em; color: var(--gold); }
  .germ-badge__germs { font-weight: 800; font-size: 4em; }

  .product-name {
    position: absolute;
    left: 0; right: 0; top: 56.5%;
    text-align: center;
    font-style: italic;
    font-weight: 900;
    line-height: 0.9;
    text-shadow: 0 0.04em 0.08em rgba(10,40,100,.55);
  }
  .product-name__line1 { display: block; font-size: 12.5em; margin-right: 14%; letter-spacing: -0.01em; }
  .product-name__line2 { display: block; font-size: 18em; letter-spacing: -0.03em; }

  .claim {
    position: absolute;
    left: 5%; right: 7%; top: 73.2%;
    height: 4.6%;
    background: linear-gradient(90deg, var(--white) 0%, var(--white) 70%, var(--mist-blue) 100%);
    border-radius: 3em 1em 3em 1em;
    transform: skewX(-14deg);
    display: flex; align-items: center; justify-content: center;
    box-shadow: 0 0.4em 0.8em rgba(0,30,80,.35);
  }
  .claim__text {
    transform: skewX(14deg);
    font-style: italic;
    font-weight: 800;
    font-size: 4.6em;
    color: var(--navy);
    white-space: nowrap;
    letter-spacing: -0.01em;
  }
  .claim__accent { color: var(--brand-blue); }

  .benefits {
    position: absolute;
    left: 0; right: 0; top: 79.3%;
    text-align: center;
    font-family: "Oswald", sans-serif;
    font-weight: 500;
    text-transform: uppercase;
    line-height: 1.3;
    font-size: 4.5em;
    white-space: nowrap;
  }
  .benefits__lead { display: block; color: var(--gold); }
  .benefits__sub { display: block; color: var(--white); }

  .uses {
    position: absolute;
    left: 7%; top: 87.3%;
    display: flex;
    gap: 3em;
    list-style: none;
  }
  .use {
    display: flex; flex-direction: column; align-items: center;
    width: 16em;
  }
  .use__icon { width: 16em; height: 16em; display: block; }
  .use__name {
    margin-top: 0.3em;
    font-family: "Oswald", sans-serif;
    font-weight: 500;
    font-size: 3.2em;
    text-transform: uppercase;
    white-space: nowrap;
  }

  .volume {
    position: absolute;
    right: 0;
    background: var(--gold);
    clip-path: polygon(14% 0, 100% 0, 100% 100%, 0 100%);
    display: flex; align-items: baseline; justify-content: center;
    font-family: "Oswald", sans-serif;
    font-weight: 600;
    line-height: 1;
    padding-top: 1.5em;
  }
  .volume__num { color: var(--brand-blue); }
  .volume__unit { color: var(--white); }
  .label--500 .volume { left: 64%; top: 89.8%; bottom: 0; padding-left: 3em; }
  .label--500 .volume__num { font-size: 11em; }
  .label--500 .volume__unit { font-size: 6em; }
  .label--1l .volume { left: 69%; top: 88.2%; height: 9.4%; padding-left: 4em; }
  .label--1l .volume__num { font-size: 14em; }
  .label--1l .volume__unit { font-size: 9em; }
</style>
</head>
<body>
<svg width="0" height="0" style="position:absolute" aria-hidden="true">
  <defs>
    <symbol id="icon-toilet" viewBox="0 0 40 40">
      <circle cx="20" cy="20" r="18.5" fill="#0677BA" stroke="#fff" stroke-width="2"/>
      <g fill="none" stroke="#fff" stroke-width="1.6" stroke-linejoin="round">
        <rect x="13" y="9" width="14" height="6" rx="1"/>
        <path d="M12 18h16c0 4-3 7-6 7h-4c-3 0-6-3-6-7z"/>
        <path d="M16 25l-1 6h10l-1-6"/>
      </g>
    </symbol>
    <symbol id="icon-bath" viewBox="0 0 40 40">
      <circle cx="20" cy="20" r="18.5" fill="#0677BA" stroke="#fff" stroke-width="2"/>
      <g fill="none" stroke="#fff" stroke-width="1.6" stroke-linejoin="round">
        <path d="M10 20h20v4c0 3-2 5-5 5h-10c-3 0-5-2-5-5z"/>
        <path d="M13 20v-8h5v5h-5"/>
        <path d="M24 13c0-2 1-3 3-3s3 1 3 3"/>
        <path d="M14 29l-1 2M26 29l1 2"/>
      </g>
    </symbol>
    <symbol id="icon-sink" viewBox="0 0 40 40">
      <circle cx="20" cy="20" r="18.5" fill="#0677BA" stroke="#fff" stroke-width="2"/>
      <g fill="none" stroke="#fff" stroke-width="1.6" stroke-linejoin="round">
        <rect x="13" y="8" width="14" height="9" rx="1"/>
        <path d="M17 14l4-4 2 2"/>
        <path d="M11 19h18c0 4-3 6-6 6h-6c-3 0-6-2-6-6z"/>
        <path d="M18 25v6h4v-6"/>
      </g>
    </symbol>
  </defs>
</svg>

<main class="sheet">
  <section class="label label--500">
    <div class="label-photo" role="img" aria-label="Photo of a bright modern bathroom with shower, washbasin and tiled bath, framed by a blue water splash"></div>
    <div class="label-band"></div>

    <div class="brand">
      <span class="brand-dot"></span>
      <span class="brand-name">Vorlix</span>
    </div>

    <h1 class="product-name">
      <span class="product-name__line1">Sanitary</span>
      <span class="product-name__line2">Cleaner</span>
    </h1>

    <div class="claim"><p class="claim__text">Cleans, descales <span class="claim__accent">&amp; freshens.</span></p></div>

    <p class="benefits">
      <span class="benefits__lead">Ideal for quick and powerful cleaning.</span>
      <span class="benefits__sub">A ready-to-use product for everyday use</span>
    </p>

    <ul class="uses">
      <li class="use"><svg class="use__icon"><use href="#icon-toilet"/></svg><span class="use__name">Sanitary</span></li>
      <li class="use"><svg class="use__icon"><use href="#icon-bath"/></svg><span class="use__name">Bathroom</span></li>
      <li class="use"><svg class="use__icon"><use href="#icon-sink"/></svg><span class="use__name">Wet areas</span></li>
    </ul>

    <div class="volume"><span class="volume__num">500</span><span class="volume__unit">ml</span></div>
  </section>

  <section class="label label--1l">
    <div class="label-photo" role="img" aria-label="Photo of a bright modern bathroom with shower, washbasin and tiled bath, framed by a blue water splash"></div>
    <div class="label-band"></div>

    <div class="brand">
      <span class="brand-dot"></span>
      <span class="brand-name">Vorlix</span>
    </div>

    <div class="germ-badge">
      <span class="germ-badge__kills">Kills</span>
      <span class="germ-badge__rate">99.99%</span>
      <span class="germ-badge__germs">Germs</span>
    </div>

    <h1 class="product-name">
      <span class="product-name__line1">Sanitary</span>
      <span class="product-name__line2">Cleaner</span>
    </h1>

    <div class="claim"><p class="claim__text">Cleans, descales <span class="claim__accent">&amp; freshens.</span></p></div>

    <p class="benefits">
      <span class="benefits__lead">Ideal for quick and powerful cleaning.</span>
      <span class="benefits__sub">A ready-to-use product for everyday use</span>
    </p>

    <ul class="uses">
      <li class="use"><svg class="use__icon"><use href="#icon-toilet"/></svg><span class="use__name">Sanitary</span></li>
      <li class="use"><svg class="use__icon"><use href="#icon-bath"/></svg><span class="use__name">Bathroom</span></li>
      <li class="use"><svg class="use__icon"><use href="#icon-sink"/></svg><span class="use__name">Wet areas</span></li>
    </ul>

    <div class="volume"><span class="volume__num">1</span><span class="volume__unit">L.</span></div>
  </section>
</main>
</body>
</html>
```